We need a modern WIX website for Brightform Beam Services Australia (Laser/Industrial/Engineering)

We need a website for Wix (coded) for our laser restoration and industrial cleaning business.

It will need to be 4-6 pages.
Pages may include:
Home
About
Why Laser
Capabilities
There needs to be a contact / quote form

We do not want boring institutional design, so please do try to be a little creative (but not artsy, more engineering / laser etc). We hesitate with boxy wordpress looking templates, so please bring in strip backgrounds and sliders etc;

Our brand colours are blue and red, but a sharp modern site relative to the industry and work is important.

We envision the home page to take visitors on a informed journey of who, what, why, how, explaining the capability of laser science across contaminants, industries and surfaces.

We envision the home page to be strips:
- landing
- intro

-Why choose laser / What is laser cleaning
Minimum downtime, no surface damage, no environmental impact, no mess, no waste, complete restoration (we have an explainer video)

- Contaminants
Bacteria, Rust, Corrosion, Oxides, Grease, Oil, Paint, Stains, Mold, Soot / Carbon, Graffiti, Coatings, Dirt, Residue

- Surfaces
Metals, Engines/Parts/Components, Tools, Machinery, Bricks/Blockwork, Concrete, Paint, Stone, Wood, Aluminium

- Industries
Medical/Sterile, Hospitality, Bio Hazardous, Construction, Infrastructure, Property, Industrial, Engineer, Automotive, Marine, Heritage, Non Destructive Testing,

----
Here is some info on the company below:

"Background Information - Brightform Beam Services Australia (BBSA) is a leading provider of advanced laser restoration services for the residential, commercial, medical, hazardous and industrial sectors, offering waste free, chemical free and damage free complete restoration of metals, concrete, wood, stone and heritage, hygiene and hazard surfaces, with complete removal of coatings, bacteria, paint, rust, graffiti, mold and fire ash (soot), and preparation and treating for welding and bonding.
Servicing Melbourne and Victoria, with additional services available Australia wide, BBSA offers a 24/7 call-out service to your site.
With no downtime to your operations, we offer a timely resolution to your cleaning and maintenance needs."

We have attached some inspiration of websites we like the flow/feel of, but feel free to put your best designs forward.

You are welcome to use dummy headers and text at this stage, as design and feel is most important, and we can add text later.

```html
<!DOCTYPE html>
<html lang="en">
<head>
<meta charset="utf-8">
<title>Brightform Beam Services Australia</title>
<link rel="stylesheet" href="https://fonts.googleapis.com/css2?family=Oswald:wght@300;500&family=Krona+One&family=Lato:wght@400;700&display=swap">
<style>
:root{
  --red:#e31e24;
  --blue:#1a6fc0;
  --blue-deep:#0f5aa5;
  --ink:#0d0d0d;
  --white:#ffffff;
}
*{margin:0;padding:0;box-sizing:border-box}
html,body{width:1200px;height:4415px;overflow:hidden;background:var(--white)}
body{position:relative;font-family:'Lato',sans-serif;color:var(--ink)}
.abs{position:absolute}
.wide{font-family:'Krona One',sans-serif;text-transform:uppercase;letter-spacing:.5px}
.heading,.hero h1,.about h2{font-family:'Oswald',sans-serif;font-weight:500}

/* top bar */
.topbar{left:0;top:0;width:1200px;height:55px;background:var(--red);color:var(--white);font-size:12px}
.topbar .item{top:21px}
.topbar .sep{top:16px;width:1px;height:22px;background:rgba(255,255,255,.7)}

/* nav */
.nav{left:0;top:55px;width:1200px;height:86px;background:var(--white);border-bottom:1px solid #ddd}
.brand{display:flex;align-items:center;gap:10px}
.brand .mark{width:22px;height:22px;background:var(--red)}
.brand .name{font-family:'Krona One',sans-serif;font-size:30px;color:var(--blue);letter-spacing:1px}
.nav .link{top:37px;font-size:12px;color:var(--ink)}
.nav .link.active{color:var(--red)}
.nav .cta{left:951px;top:22px;width:146px;height:43px;background:var(--blue);color:var(--white);font-size:11px;display:flex;align-items:center;justify-content:center;box-shadow:3px 3px 0 #7fb1e3}

/* hero */
.hero{left:0;top:141px;width:1200px;height:622px;background:#0b0b0b;overflow:hidden}
.hero .photo{left:0;top:0;width:1200px;height:622px;background:radial-gradient(circle at 800px 260px,#c8563a 0,#6b2a24 14%,#1e2a40 40%,#0d1018 70%,#0b0b0b 100%)}
.hero .kicker{left:111px;top:91px;color:var(--white);font-size:11px}
.hero h1{left:111px;top:112px;width:600px;color:var(--white);font-size:50px;line-height:60px}
.btn{display:flex;align-items:center;gap:14px;background:var(--white);color:var(--ink);font-size:13px;padding-left:12px}
.btn .mark{width:30px;height:30px;background:var(--blue)}
.hero .btn{left:111px;top:313px;width:228px;height:55px}
.dot{width:10px;height:10px;border-radius:50%;background:#777}
.dot.on{background:var(--white)}

/* about */
.about{left:0;top:763px;width:1200px;height:697px;background:repeating-linear-gradient(135deg,#151515 0 6px,#111 6px 12px)}
.outline{font-family:'Oswald',sans-serif;font-weight:300;color:transparent;-webkit-text-stroke:1.5px rgba(0,0,0,.12);text-transform:uppercase;white-space:nowrap}
.about .side{left:-54px;top:200px;transform:rotate(-90deg);font-size:120px;-webkit-text-stroke:1.5px rgba(255,255,255,.13);letter-spacing:6px}
.about .frame-red{left:178px;top:37px;width:285px;height:400px;border:8px solid var(--red)}
.about .frame-white{left:545px;top:180px;width:46px;height:398px;border:6px solid var(--white);border-left:none}
.about .photo{left:209px;top:82px;width:357px;height:496px;background:linear-gradient(160deg,#2d4f55,#1c3940 45%,#6a7b5a 70%,#f1e6b4 85%,#3a3528)}
.about .block{left:209px;top:578px;width:146px;height:51px;background:var(--red)}
.about .text{left:658px;top:72px;width:431px;color:var(--white)}
.label{font-size:11px;color:var(--red);letter-spacing:3px}
.about h2{font-size:32px;line-height:44px;margin-top:12px;text-transform:uppercase}
.about p{font-size:14.5px;line-height:25.7px;text-align:justify;margin-top:12px}
.about .btn{left:660px;top:569px;width:214px;height:57px}

/* carousels */
.section-title{left:0;width:1200px;text-align:center}
.section-title .big{font-size:130px;letter-spacing:10px;line-height:1}
.heading{font-size:32px;text-transform:uppercase}
.arrow{width:28px;height:28px;border-radius:50%;background:var(--ink);display:flex;align-items:center;justify-content:center}
.arrow.light{background:var(--white)}
.tri-label{width:220px;text-align:center;font-size:15px}
.contaminants{left:0;top:1460px;width:1200px;height:440px;background:var(--white)}
.surfaces{left:0;top:2920px;width:1200px;height:491px;background:var(--white)}
.icon{fill:none;stroke:#fff;stroke-width:3;stroke-linecap:round;stroke-linejoin:round}

/* why laser */
.why{left:0;top:1900px;width:1200px;height:843px;background:linear-gradient(160deg,var(--blue) 0,var(--blue-deep) 100%)}
.why .outline{-webkit-text-stroke:1.5px rgba(255,255,255,.35)}
.card{background:var(--white);padding:3px}
.card .img{width:100%;height:218px}
.card .cap{height:48px;display:flex;align-items:center;justify-content:center;text-align:center;font-size:11px;line-height:20px;color:var(--ink)}
.video{left:115px;top:2431px;width:970px;height:489px;border:3px solid var(--red);background:radial-gradient(circle at 400px 200px,#7a5a3c 0,#3b3430 35%,#1a1a1c 80%)}
.video .play{left:455px;top:230px;width:60px;height:60px;border-radius:50%;background:var(--red);display:flex;align-items:center;justify-content:center}
.video .tag{right:32px;top:24px;color:var(--white);font-family:'Krona One',sans-serif;font-size:24px;letter-spacing:1px}

/* industries */
.industries{left:0;top:3411px;width:1200px;height:546px;background:#101010}
.industries .outline{-webkit-text-stroke:1.5px rgba(255,255,255,.1)}
.ind-card{background:var(--white);padding:3px;width:283px;height:269px}
.ind-card .img{height:218px}
.ind-card .cap{height:45px;display:flex;align-items:center;justify-content:center;font-size:11px}

/* footer */
.footer{left:0;top:3957px;width:1200px;height:458px;background:#0a0a0a;color:var(--white)}
.footer h4{font-family:'Krona One',sans-serif;font-size:12px;font-weight:400;letter-spacing:1px;text-transform:uppercase}
.footer .small{font-size:13px;line-height:26px;white-space:nowrap}
.footer input{width:228px;height:46px;border:none;padding:0 16px;font-family:'Lato',sans-serif;font-size:12px;color:#777}
.footer .subscribe{width:185px;height:55px;background:var(--red);color:var(--white);font-weight:700;font-size:15px;display:flex;align-items:center;padding-left:18px}
.ico{width:32px;height:32px;background:var(--white);border-radius:4px;display:flex;align-items:center;justify-content:center}
.footer .quick div{font-size:14px;line-height:34px;display:flex;align-items:center;gap:10px}
.footer .rule{left:111px;top:376px;width:978px;height:1px;background:rgba(255,255,255,.5)}
.footer .copy{left:0;top:414px;width:1200px;text-align:center;font-size:12px}
</style>
</head>
<body>

<!-- top bar -->
<div class="abs topbar">
  <svg class="abs" style="left:112px;top:18px" width="18" height="18" viewBox="0 0 24 24" fill="#fff"><path d="M6.6 10.8a15 15 0 0 0 6.6 6.6l2.2-2.2c.3-.3.7-.4 1-.2 1.1.4 2.3.6 3.6.6.6 0 1 .4 1 1V20c0 .6-.4 1-1 1C10.6 21 3 13.4 3 4c0-.6.4-1 1-1h3.5c.6 0 1 .4 1 1 0 1.3.2 2.5.6 3.6.1.3 0 .7-.2 1z"/></svg>
  <div class="abs sep" style="left:146px"></div>
  <div class="abs item wide" style="left:168px">Call:+61 3 9000 4400</div>
  <svg class="abs" style="left:404px;top:19px" width="18" height="14" viewBox="0 0 24 18" fill="#fff"><path d="M0 0h24v18H0z"/><path d="M1 1l11 8 11-8" stroke="#e31e24" stroke-width="2" fill="none"/></svg>
  <div class="abs sep" style="left:441px"></div>
  <div class="abs item wide" style="left:463px">Mail:info@brightformbeam.au</div>
</div>

<!-- nav -->
<div class="abs nav">
  <div class="abs brand" style="left:103px;top:24px"><span class="mark"></span><span class="name">BBSA</span></div>
  <div class="abs link wide active" style="left:434px">Home</div>
  <div class="abs link wide" style="left:526px">About</div>
  <div class="abs link wide" style="left:633px">Why Laser</div>
  <div class="abs link wide" style="left:783px">Capabilities</div>
  <div class="abs cta wide">Contact Us</div>
</div>

<!-- hero -->
<section class="abs hero">
  <div class="abs photo" role="img" aria-label="Laser cutting head throwing bright sparks onto a metal surface"></div>
  <div class="abs kicker wide">Brightform Beam Services Australia</div>
  <h1 class="abs">We are a laser restoration and<br>industrial cleaning<br>business</h1>
  <div class="abs btn wide"><span class="mark"></span>Get Started</div>
  <svg class="abs" style="left:0;top:416px" width="1200" height="206" viewBox="0 0 1200 206">
    <polygon points="0,0 600,206 1200,26 1200,206 0,206" fill="#0d0d0d"/>
    <polygon points="0,0 600,190 1200,26 1200,40 600,206 0,14" fill="#e31e24"/>
    <polygon points="200,70 600,190 1000,80 600,150" fill="#e31e24" opacity=".85"/>
  </svg>
  <div class="abs dot" style="left:583px;top:505px"></div>
  <div class="abs dot" style="left:605px;top:505px"></div>
  <div class="abs dot on" style="left:627px;top:505px"></div>
</section>

<!-- about -->
<section class="abs about">
  <div class="abs outline side">About</div>
  <div class="abs frame-red"></div>
  <div class="abs frame-white"></div>
  <div class="abs photo" role="img" aria-label="Industrial laser nozzle glowing over a metal part"></div>
  <div class="abs block"></div>
  <div class="abs text">
    <div class="label wide">About Us</div>
    <h2>Welcome to Brightform Beam<br>Services Australia</h2>
    <p>Brightform Beam Services Australia (BBSA) is a leading provider of advanced laser restoration services for the residential, commercial, medical, hazardous and industrial sectors, offering waste free, chemical free and damage free complete restoration of metals, concrete, wood, stone and heritage, hygiene and hazard surfaces, with complete removal of coatings, bacteria, paint, rust, graffiti, mold and fire ash (soot), and preparation and treating for welding and bonding. Servicing Melbourne and Victoria, with additional services available Australia wide, BBSA offers a 24/7 call-out service to your site.</p>
    <p style="margin-top:26px">With no downtime to your operations, we offer a timely resolution to your cleaning and maintenance needs.</p>
  </div>
  <div class="abs btn wide"><span class="mark"></span>Read More</div>
</section>

<!-- contaminants -->
<section class="abs contaminants">
  <div class="abs section-title" style="top:30px"><div class="outline big">Contaminants</div></div>
  <div class="abs section-title label wide" style="top:60px">BBSA</div>
  <div class="abs section-title heading" style="top:82px">Our Contaminants</div>
  <svg class="abs" style="left:0;top:177px" width="1200" height="154">
    <polygon points="206,0 303,154 109,154" fill="#e31e24"/>
    <polygon points="301,0 495,0 398,154" fill="#1a6fc0"/>
    <polygon points="598,0 695,154 501,154" fill="#e31e24"/>
    <polygon points="702,0 896,0 799,154" fill="#1a6fc0"/>
    <polygon points="991,0 1088,154 894,154" fill="#e31e24"/>
    <!-- bacteria -->
    <g class="icon" transform="translate(206,100)">
      <ellipse cx="-4" cy="0" rx="20" ry="11" transform="rotate(-35)"/>
      <circle cx="-8" cy="2" r="2.5"/><circle cx="0" cy="-6" r="2.5"/>
      <circle cx="20" cy="-18" r="4"/><circle cx="22" cy="2" r="3"/><circle cx="14" cy="20" r="6"/>
    </g>
    <!-- nut -->
    <g class="icon" transform="translate(398,50)">
      <polygon points="24,0 12,21 -12,21 -24,0 -12,-21 12,-21"/>
      <circle r="10"/><circle r="5"/>
    </g>
    <!-- atom -->
    <g class="icon" transform="translate(598,100)">
      <ellipse rx="26" ry="9"/><ellipse rx="26" ry="9" transform="rotate(60)"/><ellipse rx="26" ry="9" transform="rotate(-60)"/>
      <circle r="3" fill="#fff"/>
    </g>
    <!-- nut -->
    <g class="icon" transform="translate(799,50)">
      <polygon points="24,0 12,21 -12,21 -24,0 -12,-21 12,-21"/>
      <circle r="10"/><circle r="5"/>
    </g>
    <!-- spray bottle -->
    <g class="icon" transform="translate(991,100)">
      <rect x="-10" y="-6" width="20" height="30" rx="3"/>
      <path d="M-6 -6v-8h12v8M-4 -14v-6h10l4 4"/>
      <path d="M-18 -22l-3 -2M-18 -17h-4M-18 -12l-3 2"/>
    </g>
  </svg>
  <div class="abs arrow" style="left:34px;top:257px"><svg width="10" height="12" viewBox="0 0 10 12"><path d="M8 1L2 6l6 5" stroke="#fff" stroke-width="2" fill="none"/></svg></div>
  <div class="abs arrow" style="left:1123px;top:257px"><svg width="10" height="12" viewBox="0 0 10 12"><path d="M2 1l6 5-6 5" stroke="#fff" stroke-width="2" fill="none"/></svg></div>
  <div class="abs tri-label wide" style="left:96px;top:352px">Bacteria</div>
  <div class="abs tri-label wide" style="left:288px;top:352px">Rust</div>
  <div class="abs tri-label wide" style="left:488px;top:352px">Oxides</div>
  <div class="abs tri-label wide" style="left:689px;top:352px">Rust</div>
  <div class="abs tri-label wide" style="left:881px;top:352px">Grease</div>
</section>

<!-- why laser -->
<section class="abs why">
  <div class="abs section-title" style="top:45px"><div class="outline big">Choose Laser</div></div>
  <div class="abs section-title label wide" style="top:81px;color:#fff">Laser</div>
  <div class="abs section-title heading" style="top:104px;color:#fff">Why Choose Laser</div>
  <div class="abs card" style="left:103px;top:205px;width:236px"><div class="img" role="img" aria-label="Grimy industrial escalator interior" style="background:linear-gradient(180deg,#3b3b38,#1c1c1a)"></div><div class="cap wide">No<br>Surface Damage</div></div>
  <div class="abs card" style="left:355px;top:205px;width:238px"><div class="img" role="img" aria-label="Cracked dry earth under a warm sky" style="background:linear-gradient(180deg,#e6b57c,#b87a48 55%,#8a5a36)"></div><div class="cap wide">No Environmental<br>Impact</div></div>
  <div class="abs card" style="left:607px;top:205px;width:238px"><div class="img" role="img" aria-label="Worker in protective gear blasting a surface" style="background:linear-gradient(180deg,#8c949a,#4f5962 60%,#3a3f44)"></div><div class="cap wide">Minimum<br>Downtime</div></div>
  <div class="abs card" style="left:859px;top:205px;width:238px"><div class="img" role="img" aria-label="Gloved hand brushing finish onto timber boards" style="background:linear-gradient(180deg,#6c5a4a,#a0785a 50%,#5a3e2a)"></div><div class="cap wide">Complete<br>Restoration</div></div>
  <div class="abs arrow light" style="left:34px;top:342px"><svg width="10" height="12" viewBox="0 0 10 12"><path d="M8 1L2 6l6 5" stroke="#0d0d0d" stroke-width="2" fill="none"/></svg></div>
  <div class="abs arrow light" style="left:1123px;top:342px"><svg width="10" height="12" viewBox="0 0 10 12"><path d="M2 1l6 5-6 5" stroke="#0d0d0d" stroke-width="2" fill="none"/></svg></div>
</section>

<div class="abs video" role="img" aria-label="Explainer video still of a laser head sending out sparks">
  <div class="abs tag">BBSA</div>
  <div class="abs play"><svg width="20" height="22" viewBox="0 0 20 22"><path d="M3 2l15 9-15 9z" fill="#fff"/></svg></div>
</div>

<!-- surfaces -->
<section class="abs surfaces">
  <div class="abs section-title" style="top:77px"><div class="outline big">Surfaces</div></div>
  <div class="abs section-title label wide" style="top:106px">BBSA</div>
  <div class="abs section-title heading" style="top:128px">Our Surfaces</div>
  <svg class="abs" style="left:0;top:239px" width="1200" height="153">
    <polygon points="208,0 305,153 111,153" fill="#e31e24"/>
    <polygon points="303,0 497,0 400,153" fill="#1a6fc0"/>
    <polygon points="603,0 700,153 506,153" fill="#e31e24"/>
    <polygon points="702,0 896,0 799,153" fill="#1a6fc0"/>
    <polygon points="991,0 1088,153 894,153" fill="#e31e24"/>
    <!-- metal beams -->
    <g class="icon" transform="translate(208,100)">
      <path d="M-22 20l26 -34h16l-26 34z"/>
      <path d="M-10 24l26 -34h10l-26 34z"/>
      <path d="M-22 20h12M-12 24h12"/>
    </g>
    <!-- tools -->
    <g class="icon" transform="translate(400,50)">
      <path d="M-18 -18l36 36M18 -18l-36 36"/>
      <circle cx="-20" cy="-20" r="6"/><circle cx="20" cy="20" r="6"/>
      <rect x="14" y="-24" width="10" height="8" transform="rotate(45 19 -20)"/>
    </g>
    <!-- machinery -->
    <g class="icon" transform="translate(603,100)">
      <rect x="-20" y="-20" width="40" height="16" rx="2"/>
      <path d="M-12 -4v8h24v-8M0 4v6"/>
      <circle cx="0" cy="18" r="7"/><circle cx="0" cy="18" r="2"/>
    </g>
    <!-- paint roller -->
    <g class="icon" transform="translate(799,50)">
      <rect x="-20" y="-24" width="32" height="14" rx="3"/>
      <path d="M12 -17h8v12h-20v8"/>
      <rect x="-4" y="3" width="8" height="20" rx="2"/>
    </g>
    <!-- spring -->
    <g class="icon" transform="translate(991,100)">
      <path d="M-18 -26l36 6l-36 6l36 6l-36 6l36 6l-36 6l36 6l-36 6"/>
    </g>
  </svg>
  <div class="abs arrow" style="left:36px;top:320px"><svg width="10" height="12" viewBox="0 0 10 12"><path d="M8 1L2 6l6 5" stroke="#fff" stroke-width="2" fill="none"/></svg></div>
  <div class="abs arrow" style="left:1124px;top:320px"><svg width="10" height="12" viewBox="0 0 10 12"><path d="M2 1l6 5-6 5" stroke="#fff" stroke-width="2" fill="none"/></svg></div>
  <div class="abs tri-label wide" style="left:98px;top:415px">Metals</div>
  <div class="abs tri-label wide" style="left:290px;top:415px">Tools</div>
  <div class="abs tri-label wide" style="left:493px;top:415px">Machinery</div>
  <div class="abs tri-label wide" style="left:689px;top:415px">Paint</div>
  <div class="abs tri-label wide" style="left:883px;top:415px">Aluminium</div>
</section>

<!-- industries -->
<section class="abs industries">
  <div class="abs section-title" style="top:43px"><div class="outline big">Industries</div></div>
  <div class="abs section-title label wide" style="top:76px">BBSA</div>
  <div class="abs section-title heading" style="top:108px;color:#fff">Our Industries</div>
  <div class="abs ind-card" style="left:110px;top:203px"><div class="img" role="img" aria-label="Sterile laboratory with glass apparatus" style="background:linear-gradient(150deg,#dfe7ee,#a9b8c6 55%,#6d7c8a)"></div><div class="cap wide">Medical/Sterile</div></div>
  <div class="abs ind-card" style="left:458px;top:203px"><div class="img" role="img" aria-label="Clean production floor with rows of machines" style="background:linear-gradient(180deg,#cfd6dc,#9aa7b0 60%,#7fa08a)"></div><div class="cap wide">Hospitality</div></div>
  <div class="abs ind-card" style="left:806px;top:203px"><div class="img" role="img" aria-label="Dry ice cleaning tool releasing vapour" style="background:linear-gradient(160deg,#1a1a1a,#444 55%,#bdbdbd)"></div><div class="cap wide">Bio Hazardous</div></div>
  <div class="abs arrow light" style="left:35px;top:332px"><svg width="10" height="12" viewBox="0 0 10 12"><path d="M8 1L2 6l6 5" stroke="#0d0d0d" stroke-width="2" fill="none"/></svg></div>
  <div class="abs arrow light" style="left:1123px;top:332px"><svg width="10" height="12" viewBox="0 0 10 12"><path d="M2 1l6 5-6 5" stroke="#0d0d0d" stroke-width="2" fill="none"/></svg></div>
</section>

<!-- footer -->
<footer class="abs footer">
  <div class="abs brand" style="left:115px;top:100px"><span class="mark"></span><span class="name" style="color:#fff;font-size:28px">BBSA</span></div>

  <div class="abs" style="left:386px;top:99px">
    <h4>Subscribe Us</h4>
    <div class="small" style="margin-top:12px;width:230px;white-space:normal">BBSA offers a 24/7 call-out service to your site</div>
    <input type="text" placeholder="Enter The Email" style="margin-top:10px">
    <div class="subscribe" style="margin-top:22px">Subscribe</div>
  </div>

  <div class="abs" style="left:696px;top:99px">
    <h4>Contact Us</h4>
    <div style="position:relative;margin-top:30px;height:60px">
      <div class="ico abs" style="left:0;top:0"><svg width="14" height="18" viewBox="0 0 14 18"><path d="M7 0a7 7 0 0 0-7 7c0 5 7 11 7 11s7-6 7-11a7 7 0 0 0-7-7zm0 10a3 3 0 1 1 0-6 3 3 0 0 1 0 6z" fill="#0d0d0d"/></svg></div>
      <div class="abs small" style="left:41px;top:-8px;line-height:27px">BBSA<br>Melbourne VIC</div>
    </div>
    <div style="position:relative;margin-top:10px;height:60px">
      <div class="ico abs" style="left:0;top:0"><svg width="16" height="16" viewBox="0 0 24 24" fill="#0d0d0d"><path d="M6.6 10.8a15 15 0 0 0 6.6 6.6l2.2-2.2c.3-.3.7-.4 1-.2 1.1.4 2.3.6 3.6.6.6 0 1 .4 1 1V20c0 .6-.4 1-1 1C10.6 21 3 13.4 3 4c0-.6.4-1 1-1h3.5c.6 0 1 .4 1 1 0 1.3.2 2.5.6 3.6.1.3 0 .7-.2 1z"/></svg></div>
      <div class="abs small" style="left:41px;top:3px">+61 3 9000 4400</div>
    </div>
    <div style="position:relative;margin-top:8px;height:40px">
      <div class="ico abs" style="left:0;top:0"><svg width="16" height="12" viewBox="0 0 24 18"><path d="M0 0h24v18H0z" fill="#0d0d0d"/><path d="M1 1l11 8 11-8" stroke="#fff" stroke-width="2" fill="none"/></svg></div>
      <div class="abs small" style="left:41px;top:3px">info@brightformbeam.au</div>
    </div>
  </div>

  <div class="abs quick" style="left:927px;top:99px">
    <h4>Quick Links</h4>
    <div style="margin-top:18px"><svg width="12" height="12" viewBox="0 0 12 12"><path d="M1 6h9M6 2l4 4-4 4" stroke="#fff" stroke-width="2" fill="none"/></svg>Home</div>
    <div><svg width="12" height="12" viewBox="0 0 12 12"><path d="M1 6h9M6 2l4 4-4 4" stroke="#fff" stroke-width="2" fill="none"/></svg>About</div>
    <div><svg width="12" height="12" viewBox="0 0 12 12"><path d="M1 6h9M6 2l4 4-4 4" stroke="#fff" stroke-width="2" fill="none"/></svg>Why Laser</div>
    <div><svg width="12" height="12" viewBox="0 0 12 12"><path d="M1 6h9M6 2l4 4-4 4" stroke="#fff" stroke-width="2" fill="none"/></svg>Capabilities</div>
    <div><svg width="12" height="12" viewBox="0 0 12 12"><path d="M1 6h9M6 2l4 4-4 4" stroke="#fff" stroke-width="2" fill="none"/></svg>Contact Us</div>
  </div>

  <div class="abs rule"></div>
  <div class="abs copy">Copyrights@2023.Brightform Beam Services Australia.All Rights Reserved</div>
</footer>

</body>
</html>
```